Brenwick Structures Construction Company Seeking Modern Website

We are a small construction company wanting to create a web presence. We don't have much in the way of current content but will get photos as they come in. Attached is a picture of our business card.
The pages we would like on the menu are:
Home
Portfolio
Product Specs
Testimonials
Our Process
Contact
Some designs we like are:
http://www.tovasheds-example.com/
http://www.qrnstructures-example.com/
http://dunholtbarns-example.com/
http://pellingframes-example.com/
Not much requirements other than that so feel free to be creative!
Updates
Target Market(s)
Construction
Commercial and Residential Buildings
Industry/Entity Type
Construction Company
Number of Pages Required
5+ page
Look and feel

```html
<!DOCTYPE html>
<html lang="en">
<head>
<meta charset="utf-8">
<title>Brenwick Structures – Construction Company</title>
<link href="https://fonts.googleapis.com/css2?family=Open+Sans:wght@400;600;700&display=swap" rel="stylesheet">
<style>
:root{
  --blue:#0f9ad8;
  --blue-dark:#0b7fbf;
  --blue-deep:#0a6aa6;
  --grey-tab:#9fa4a8;
  --ink:#3a3a3a;
  --muted:#555;
  --line:#e4e4e4;
  --white:#fff;
  --header-bg:#f4f2ee;
}
*{margin:0;padding:0;box-sizing:border-box}
html,body{width:1200px;height:2539px;overflow:hidden}
body{font-family:"Open Sans",Arial,sans-serif;color:var(--ink);background:var(--white);position:relative}
.abs{position:absolute}

/* header */
.site-header{position:absolute;left:0;top:0;width:1200px;height:142px;background:var(--header-bg)}
.brand{position:absolute;left:98px;top:30px}
.brand-name{font-size:46px;font-weight:600;color:var(--blue);letter-spacing:-.5px;line-height:1.1}
.brand-tag{font-size:13px;font-weight:600;color:var(--blue-deep);margin-top:6px;padding-left:16px}
.call{position:absolute;left:914px;top:16px;display:flex;gap:10px;align-items:center}
.call-label{font-size:15px;font-weight:600;color:#222;line-height:1.3}
.call-number{font-size:19px;color:var(--blue);line-height:1.3}
.search{position:absolute;left:812px;top:86px;width:288px;height:32px;background:#fff;border:1px solid var(--line);display:flex}
.search span{flex:1;font-size:11px;color:#aaa;padding:8px 10px}
.search i{width:42px;border-left:1px solid var(--line);display:flex;align-items:center;justify-content:center}

/* nav */
.main-nav{position:absolute;left:0;top:142px;width:1200px;height:46px;background:linear-gradient(#22aee6,#0b8fcf)}
.main-nav ul{list-style:none;position:absolute;left:98px;top:0;display:flex;height:46px}
.main-nav li{height:46px;display:flex;align-items:center;justify-content:center;font-size:12.5px;color:#fff;text-transform:uppercase;border-right:1px solid rgba(255,255,255,.18);width:180px;gap:10px}
.main-nav li:first-child{width:180px;justify-content:flex-start;padding-left:30px}

/* hero */
.hero{position:absolute;left:0;top:188px;width:1200px;height:558px;background:linear-gradient(100deg,#3b3f45 0%,#8a8580 30%,#c9c2bb 55%,#a59e97 80%,#d0cac4 100%)}
.hero-text{position:absolute;right:100px;top:186px;text-align:right;color:#fff}
.hero-text h1{font-size:33px;font-weight:700;line-height:1.3;text-transform:uppercase;text-shadow:0 1px 3px rgba(0,0,0,.3)}
.hero-text p{font-size:20px;line-height:1.5;margin-top:12px}
.hero-arrow{position:absolute;top:425px;width:48px;height:48px;border-radius:50%;background:rgba(255,255,255,.35);display:flex;align-items:center;justify-content:center}

/* tabs */
.tab{position:absolute;top:778px;height:62px;display:flex;align-items:center;justify-content:center;gap:12px;color:#fff;font-size:21px;text-transform:uppercase}
.tab-commercial{left:98px;width:498px;background:linear-gradient(#22aee6,#0b8fcf)}
.tab-residential{left:604px;width:496px;background:var(--grey-tab)}
.tab-notch{position:absolute;left:334px;top:840px;width:0;height:0;border-left:12px solid transparent;border-right:12px solid transparent;border-top:12px solid var(--blue-dark)}
.panel{position:absolute;left:98px;top:840px;width:1004px;height:423px;background:#fff}
.panel-photo{position:absolute;left:440px;top:0;width:564px;height:423px;background:linear-gradient(90deg,rgba(255,255,255,1) 0%,rgba(190,225,240,.6) 25%,#5fb2d8 55%,#1d7fb4 85%,#3f9cc8 100%)}
.panel-body{position:absolute;left:35px;top:55px;width:450px}
.panel-body h2{font-size:25px;font-weight:400;color:var(--blue);margin-bottom:30px}
.panel-body p{font-size:12px;line-height:22.5px;color:var(--muted)}
.btn{display:inline-flex;align-items:center;justify-content:center;background:linear-gradient(#1aa6e0,#0a80c0);color:#fff;font-size:15px;font-weight:600;text-transform:uppercase}
.panel-body .btn{margin-top:42px;width:150px;height:43px}

.rule{position:absolute;left:0;top:1283px;width:1200px;height:1px;background:#ececec}

/* solutions */
.section-title{position:absolute;font-size:26px;font-weight:400}
.section-title::after{content:"";position:absolute;left:0;top:49px;width:74px;height:3px;background:var(--blue)}
.pager{position:absolute;width:44px;height:44px;border-radius:50%;background:#fff;border:1px solid var(--line);display:flex;align-items:center;justify-content:center}
.card{position:absolute;top:1381px;width:318px;height:449px;border:1px solid var(--line);background:#fff}
.card-photo{height:208px}
.card h3{font-size:16px;font-weight:600;color:var(--blue);text-transform:uppercase;margin:18px 20px 0;line-height:1.4}
.card p{font-size:12.5px;line-height:22.5px;color:var(--muted);margin:12px 20px 0}
.card .btn{position:absolute;left:20px;top:371px;width:138px;height:43px}

/* testimonials */
.testimonials{position:absolute;left:0;top:1872px;width:1200px;height:355px;background:linear-gradient(90deg,#4c5258 0%,#5f656b 40%,#3d4349 70%,#6b7075 100%)}
.testimonials .section-title{color:#fff;left:98px;top:28px}
.avatar{position:absolute;left:100px;top:125px;width:118px;height:118px;border-radius:50%;background:linear-gradient(#d8d8d8,#8d949a);border:3px solid #fff}
.quote{position:absolute;left:254px;top:146px;width:846px;font-size:11.5px;line-height:21px;color:#eee}
.quote-mark{position:absolute;font-size:40px;color:rgba(255,255,255,.5);font-family:Georgia,serif}
.author{position:absolute;left:254px;top:225px;font-size:12.5px;line-height:20px;color:#fff}
.author b{color:var(--blue);font-weight:600}

/* footer */
.site-footer{position:absolute;left:0;top:2227px;width:1200px;height:312px;background:linear-gradient(#12a2dd,#0b8acb)}
.f-col{position:absolute;top:24px;color:#fff}
.f-col h4{font-size:12.5px;font-weight:700;text-transform:uppercase;display:flex;align-items:center;gap:8px;margin-bottom:20px}
.f-col ul{list-style:none;font-size:12px;line-height:28px}
.f-col p{font-size:12px}
.f-input{margin-top:18px;width:234px;height:36px;background:#fff;font-size:11px;color:#333;padding:10px 8px}
.f-submit{margin-top:20px;width:122px;height:38px;background:#2bb8ef;font-size:15px;text-align:center;line-height:38px;text-transform:uppercase}
.social{display:flex;gap:8px}
.social span{width:33px;height:33px;border-radius:50%;border:2px solid #fff}
.contact-list{font-size:12px;line-height:28px}
.contact-list li{display:flex;gap:12px}
.contact-list b{font-weight:600}
.f-divider{position:absolute;left:0;top:247px;width:1200px;height:1px;background:rgba(255,255,255,.2)}
.copyright{position:absolute;left:0;top:270px;width:1200px;text-align:center;font-size:11.5px;color:#fff}
</style>
</head>
<body>

<header class="site-header">
  <div class="brand">
    <div class="brand-name">Brenwick Structures</div>
    <div class="brand-tag">Building Dreams, So You Can Build Memories</div>
  </div>
  <div class="call">
    <svg width="38" height="38" viewBox="0 0 38 38"><circle cx="19" cy="19" r="17" fill="none" stroke="#0f9ad8" stroke-width="2"/><path d="M13 11c1-1 2-1 3 0l2 3c.5 1 0 2-1 2.5 1 2.5 3 4.5 5.5 5.5.5-1 1.5-1.5 2.5-1l3 2c1 1 1 2 0 3-2 2-5 2-9-1s-7-7-7-10c0-2 0-3 1-4z" fill="#0f9ad8"/></svg>
    <div><div class="call-label">Call Us Today!</div><div class="call-number">+00 123456789</div></div>
  </div>
  <div class="search"><span>Search</span><i><svg width="12" height="12" viewBox="0 0 12 12"><circle cx="5" cy="5" r="3.5" fill="none" stroke="#0f9ad8" stroke-width="1.6"/><path d="M7.5 7.5l3 3" stroke="#0f9ad8" stroke-width="1.8"/></svg></i></div>
</header>

<nav class="main-nav">
  <ul>
    <li><svg width="15" height="13" viewBox="0 0 15 13"><path d="M7.5 0L0 6.5h2V13h4V9h3v4h4V6.5h2z" fill="#fff"/></svg>Home</li>
    <li>Portfolio</li>
    <li>Product Specs</li>
    <li>Testimonials</li>
    <li>Our Process</li>
    <li>Contact</li>
  </ul>
</nav>

<section class="hero" role="img" aria-label="Smiling construction manager in a yellow hard hat with colleagues reviewing plans behind him">
  <div class="hero-arrow" style="left:25px"><svg width="14" height="20" viewBox="0 0 14 20"><path d="M11 2L3 10l8 8" fill="none" stroke="#fff" stroke-width="3"/></svg></div>
  <div class="hero-arrow" style="left:1127px"><svg width="14" height="20" viewBox="0 0 14 20"><path d="M3 2l8 8-8 8" fill="none" stroke="#fff" stroke-width="3"/></svg></div>
  <div class="hero-text">
    <h1>We are a small<br>construction company</h1>
    <p>Our targets are Commercial Construction and<br>Residential Buildings</p>
  </div>
</section>

<div class="tab tab-commercial">
  <svg width="36" height="30" viewBox="0 0 36 30"><rect x="2" y="4" width="14" height="24" fill="none" stroke="#fff" stroke-width="2"/><rect x="16" y="12" width="16" height="16" fill="none" stroke="#fff" stroke-width="2"/><path d="M6 9h2M10 9h2M6 14h2M10 14h2M6 19h2M10 19h2M20 17h2M26 17h2M20 22h2M26 22h2" stroke="#fff" stroke-width="2"/></svg>
  Commercial
</div>
<div class="tab tab-residential">
  <svg width="32" height="30" viewBox="0 0 32 30"><path d="M16 3L3 14h4v13h18V14h4z" fill="none" stroke="#fff" stroke-width="2.4"/><rect x="13" y="18" width="6" height="9" fill="#fff"/></svg>
  Residential
</div>
<section class="panel">
  <div class="panel-photo" role="img" aria-label="Upward view of a modern glass office tower"></div>
  <div class="panel-body">
    <h2>Commercial Construction</h2>
    <p>Our team plans, manages and builds commercial spaces that last for decades. From offices and retail units to warehouses and clinics, we handle every stage with care, clear budgets and honest timelines. We work closely with owners and architects so each project opens on schedule and ready for business, with quality you can see in every detail.</p>
    <a class="btn">Learn More</a>
  </div>
</section>
<div class="tab-notch"></div>

<div class="rule"></div>

<h2 class="section-title" style="left:98px;top:1296px">Brenwick Structures Solutions</h2>
<div class="pager" style="left:1056px;top:1313px"><svg width="18" height="10" viewBox="0 0 18 10"><path d="M5 1L1 5l4 4M13 1l4 4-4 4" fill="none" stroke="#0f9ad8" stroke-width="1.8"/></svg></div>

<article class="card" style="left:98px">
  <div class="card-photo" role="img" aria-label="Worker in blue overalls holding a yellow hard hat and rolled plans beside a tower under construction" style="background:linear-gradient(90deg,#9fb8cf,#2a5fa5 55%,#e8c21a 75%,#5f89c4)"></div>
  <h3>Excepteur sint occaecat cupidatat</h3>
  <p>Steel frame buildings designed for strength, built fast and priced fairly for growing businesses and owners alike.</p>
  <a class="btn">Read More</a>
</article>
<article class="card" style="left:442px">
  <div class="card-photo" role="img" aria-label="Residential apartment blocks behind a green lawn under a blue sky" style="background:linear-gradient(#a8cde8 0%,#d9d2c8 45%,#6e9b4a 70%,#4f8a34 100%)"></div>
  <h3>Nam libero tempore, cum soluta.</h3>
  <p>Quality homes and residential blocks planned around families, with open layouts, bright rooms and lasting finishes.</p>
  <a class="btn">Read More</a>
</article>
<article class="card" style="left:784px">
  <div class="card-photo" role="img" aria-label="Site engineer in orange hard hat and safety vest reading plans near a crane" style="background:linear-gradient(90deg,#e98a1c 0%,#c9d64a 30%,#8fb8da 60%,#b9d3e8 100%)"></div>
  <h3>Quis autem vel eum iure reprehenderit.</h3>
  <p>Site planning, permits and project management handled by one team from the first sketch to the keys.</p>
  <a class="btn">Read More</a>
</article>

<section class="testimonials" role="img" aria-label="Blurred modern building in the background">
  <h2 class="section-title">Testmonials</h2>
  <div class="avatar" role="img" aria-label="Portrait of the client"></div>
  <span class="quote-mark" style="left:230px;top:120px">“</span>
  <p class="quote">Brenwick Structures built our new office on time and on budget. The crew kept the site clean, answered every question quickly and treated the project as if it were their own. We would gladly hire them again and recommend them to any business owner planning a new building this year.</p>
  <span class="quote-mark" style="left:1084px;top:190px">”</span>
  <div class="author"><b>Dale Hartwell</b><br>Consultant Advicer</div>
  <div class="pager" style="left:1056px;top:244px;border:none"><svg width="18" height="10" viewBox="0 0 18 10"><path d="M5 1L1 5l4 4M13 1l4 4-4 4" fill="none" stroke="#0f9ad8" stroke-width="1.8"/></svg></div>
</section>

<footer class="site-footer">
  <div class="f-col" style="left:98px">
    <h4><svg width="14" height="14" viewBox="0 0 14 14"><path d="M6 8l2-2M5 5l2-2a2.5 2.5 0 014 4l-2 2M9 9l-2 2a2.5 2.5 0 01-4-4l2-2" fill="none" stroke="#fff" stroke-width="1.8"/></svg>Quick Links</h4>
    <ul><li>Home</li><li>Portfolio</li><li>Product Specs</li><li>Testimonials</li><li>Our Process</li><li>Contact</li></ul>
  </div>
  <div class="f-col" style="left:291px">
    <h4><svg width="16" height="12" viewBox="0 0 16 12"><rect width="16" height="12" fill="#fff"/><path d="M0 0l8 6 8-6" fill="none" stroke="#0b8acb" stroke-width="1.4"/></svg>News Letter Signup</h4>
    <p>Sign-up to be notified about news</p>
    <div class="f-input">Enter Your Email</div>
    <div class="f-submit">Submit</div>
  </div>
  <div class="f-col" style="left:601px">
    <h4><svg width="16" height="14" viewBox="0 0 16 14"><path d="M9 1h6v6M15 1L8 8M12 9v4H1V3h5" fill="none" stroke="#fff" stroke-width="1.8"/></svg>Follow Us</h4>
    <div class="social"><span style="background:#3b5998"></span><span style="background:#1da1f2"></span><span style="background:#c4302b"></span><span style="background:#c63b2c"></span><span style="background:#d98b1a"></span></div>
  </div>
  <div class="f-col" style="left:863px">
    <h4><svg width="16" height="14" viewBox="0 0 16 14"><path d="M1 5c0-3 14-3 14 0v2h-4V5H5v2H1zM3 7h10l1 6H2z" fill="#fff"/></svg>Contact Us</h4>
    <ul class="contact-list">
      <li><svg width="10" height="28" viewBox="0 0 10 28"><path d="M5 20s4-4 4-7a4 4 0 00-8 0c0 3 4 7 4 7z" fill="#fff"/></svg><span><b>Office:</b> No Street Address, City Address,<br>State, Country.</span></li>
      <li><svg width="10" height="28" viewBox="0 0 10 28"><rect x="2" y="8" width="6" height="11" rx="1" fill="#fff"/></svg><span><b>Mobile:</b> (0001) 2345 6789</span></li>
      <li><svg width="10" height="28" viewBox="0 0 10 28"><rect x="1" y="10" width="8" height="8" fill="#fff"/></svg><span><b>Fax:</b> (0001) 2345 6789</span></li>
      <li><svg width="10" height="28" viewBox="0 0 10 28"><rect x="0" y="10" width="10" height="7" fill="#fff"/></svg><span><b>Mail:</b> Contact@domainname.com</span></li>
    </ul>
  </div>
  <div class="f-divider"></div>
  <div class="copyright">BRENWICK STRUCTURES. © 2015 | Privacy Policy</div>
</footer>

</body>
</html>
```